Defense Attorney Business Card Design Project/ Stationary

I am looking for a distinctive business card design for my solo law practice.
I practice criminal defense, both juvenile and adult, including DUI. I am a very experienced attorney with prior military experience. The design should convey a traditional, old school flair, but not be too stodgy or uptight. Some color. My logo should appear.
Updates

Project Deadline Extended Reason: I misunderstood how this project works and I was not prepared with my logo when this project ran the first time. Added Thursday, November 13, 2014

Project Deadline Extended
Reason: I was sent overseas on military duty last year, which interrupted this project. Thank you for your participation... I hope we can get this done this week! Thank you, Neil

Target Market(s)

Regular everyday people looking for strong, knowledgeable, authoritative representation while they are faced with criminal charges. Many have never been charged with a crime before. A reassuring air is therefore desired.

Industry/Entity Type

Business

Contact Information for Business Card

My information is:
Theodore M. Quill, Attorney at Law
785 Birch Avenue Suite 300
Oakland, California 94719
Tel: (510) 384-6125
Fax: (510) 391-7802
email: neilquilllaw@mailvine.example
web: www.neilquilllaw.example

Font styles to use
Serif
Sans Serif
Decorative

Colors
0255a3
ffffff

Requirements
Must have
• Sharp lines, bold elements. Conservative use of colors, such as deep blues, burgundy, grays for example.
• While my logo says "Theodore M. Quill", it should be modified to show "Theodore M. Quill".
Should not have
• Cliche imagery such as scales of justice, gavels, Statue of Liberty, etc.

```html
<!DOCTYPE html>
<html lang="en">
<head>
<meta charset="utf-8">
<title>Theodore M. Quill — Business Card</title>
<link rel="stylesheet" href="https://fonts.googleapis.com/css2?family=Cinzel:wght@500&family=Exo+2:wght@400;500&display=swap">
<style>
  :root{
    --navy:#0b3a55;
    --paper:#ffffff;
    --paper-shade:#f1f2f3;
    --ink-grey:#5a5d60;
    --backdrop:#e6e3de;
  }
  *{box-sizing:border-box;margin:0;padding:0}
  html,body{width:1200px;height:1085px;overflow:hidden;background:var(--backdrop)}
  .sheet{position:relative;width:1200px;height:1085px;display:flex;flex-direction:column;align-items:center;justify-content:center;gap:34px}
  .card{position:relative;width:860px;height:491px;background:linear-gradient(135deg,var(--paper) 0%,var(--paper-shade) 100%);box-shadow:0 10px 28px rgba(0,0,0,.18);overflow:hidden}

  /* front */
  .brand{position:absolute;left:90px;top:120px;display:flex;align-items:center;gap:24px}
  .brand-dot{flex:none;width:58px;height:58px;border-radius:50%;background:var(--navy)}
  .brand-text{display:flex;flex-direction:column;align-items:stretch}
  .brand-name{font-family:"Cinzel",serif;font-weight:500;font-size:42px;letter-spacing:1.5px;line-height:1.1;color:var(--navy);white-space:nowrap;padding-bottom:8px;border-bottom:2px solid var(--navy)}
  .brand-tagline{font-family:"Cinzel",serif;font-weight:500;font-size:17px;letter-spacing:6px;color:var(--navy);text-align:center;margin-top:8px;white-space:nowrap}
  .person{position:absolute;right:90px;bottom:120px;text-align:left}
  .person-name{font-family:"Exo 2",sans-serif;font-weight:500;font-size:32px;letter-spacing:3px;color:var(--ink-grey);text-transform:uppercase}
  .person-role{font-family:"Exo 2",sans-serif;font-weight:400;font-size:26px;color:var(--ink-grey);margin-top:4px}

  /* back */
  .panel{position:absolute;left:0;top:0}
  .contact{position:absolute;right:455px;text-align:right;font-family:"Exo 2",sans-serif;font-size:24px;line-height:1.3;color:var(--paper);letter-spacing:.5px;white-space:nowrap}
  .contact-phone{top:80px}
  .contact-address{top:220px}
  .contact-web{top:390px}
</style>
</head>
<body>
<main class="sheet">

  <section class="card card-front" aria-label="Card front">
    <div class="brand">
      <span class="brand-dot"></span>
      <div class="brand-text">
        <span class="brand-name">THEODORE M. QUILL</span>
        <span class="brand-tagline">ATTORNEY AT LAW</span>
      </div>
    </div>
    <div class="person">
      <p class="person-name">Owen Castell</p>
      <p class="person-role">Managing Director</p>
    </div>
  </section>

  <section class="card card-back" aria-label="Card back">
    <svg class="panel" width="860" height="491" viewBox="0 0 860 491" aria-hidden="true">
      <path fill="var(--navy)" d="M0 0 H440
        C440 30 430 50 450 62 C480 78 500 90 500 112 C500 134 480 146 450 160 C430 172 440 190 440 200
        C440 212 430 222 450 235 C480 250 500 262 500 282 C500 302 480 312 450 326 C430 336 440 350 440 358
        C440 368 430 378 450 388 C480 402 500 414 500 432 C500 450 480 460 450 470 C440 474 440 484 440 491 H0 Z"/>
      <g fill="none" stroke="var(--paper)" stroke-width="3">
        <circle cx="462" cy="112" r="22"/>
        <path d="M454 101 l5 -2 l4 8 l-3 3 c2 4 4 6 8 8 l3 -3 l8 4 l-2 5 c-12 1 -24 -11 -23 -23z" stroke-width="2.5" fill="var(--paper)"/>
        <circle cx="462" cy="282" r="22"/>
        <path d="M462 296 c-7 -9 -10 -14 -10 -19 a10 10 0 0 1 20 0 c0 5 -3 10 -10 19z" fill="var(--paper)" stroke="none"/>
        <circle cx="462" cy="277" r="3.5" fill="var(--navy)" stroke="none"/>
        <circle cx="462" cy="432" r="22"/>
        <circle cx="462" cy="432" r="13" stroke-width="2"/>
        <ellipse cx="462" cy="432" rx="6" ry="13" stroke-width="2"/>
        <path d="M449 432 h26 M451 425 h22 M451 439 h22" stroke-width="2"/>
      </g>
    </svg>
    <p class="contact contact-phone">(510) 384-6125<br>(510) 391-7802</p>
    <p class="contact contact-address">214, 6th floor,<br>Harbor Crest Road<br>OAK</p>
    <p class="contact contact-web">owen@castellfirm.example<br>castellfirm.example</p>
  </section>

</main>
</body>
</html>
```